Business card design for my company.
I would like the card's background colour to be black. You can also see our web site to get an idea of our brand. https://www.tmwhomecrafting.com.au/
- Name
- Email

```html
<!DOCTYPE html>
<html lang="en">
<head>
<meta charset="utf-8">
<title>TMW Home Crafting – Business Card</title>
<link href="https://fonts.googleapis.com/css2?family=Roboto:wght@400;500;700&display=swap" rel="stylesheet">
<style>
  :root {
    --page: #f2f2f2;
    --card: #222226;
    --green: #16994a;
    --white: #f4f4f6;
    --ghost: #2b2b30;
  }
  * { margin: 0; padding: 0; box-sizing: border-box; }
  html, body { width: 1200px; height: 987px; overflow: hidden; }
  body {
    background: var(--page);
    font-family: "Roboto", Arial, sans-serif;
    color: var(--white);
    position: relative;
  }
  .card {
    position: absolute;
    left: 245px;
    width: 709px;
    height: 405px;
    background: var(--card);
    border-left: 5px solid var(--green);
    border-bottom: 3px solid var(--green);
    overflow: hidden;
  }
  .card--front { top: 68px; }
  .card--back { top: 514px; height: 404px; }

  .brand {
    position: absolute;
    display: flex;
    align-items: center;
    gap: 12px;
    font-weight: 700;
    color: var(--white);
    white-space: nowrap;
  }
  .brand__mark { background: var(--green); flex: none; }
  .card--front .brand {
    left: 0; right: 0; top: 150px;
    justify-content: center;
    font-size: 46px;
    letter-spacing: 0.5px;
  }
  .card--front .brand__mark { width: 30px; height: 30px; }
  .card--back .brand {
    left: 26px; top: 60px;
    font-size: 30px;
    gap: 10px;
  }
  .card--back .brand__mark { width: 20px; height: 20px; }

  .website {
    position: absolute;
    left: 0; right: 0; top: 356px;
    text-align: center;
    font-size: 17px;
    letter-spacing: 0.6px;
  }
  .accent { color: var(--green); }

  .name-bar {
    position: absolute;
    left: 0; top: 223px;
    width: 10px; height: 47px;
    background: var(--green);
  }
  .person { position: absolute; left: 26px; top: 218px; }
  .person__name {
    font-size: 35px;
    font-weight: 400;
    line-height: 1.1;
    letter-spacing: 0.3px;
  }
  .person__first { color: var(--green); font-weight: 700; }
  .person__title {
    font-size: 17px;
    letter-spacing: 0.6px;
    margin-top: 1px;
  }

  .contacts {
    position: absolute;
    left: 21px; top: 286px;
    list-style: none;
  }
  .contacts li {
    display: flex;
    align-items: center;
    gap: 11px;
    height: 24px;
    font-size: 17px;
    letter-spacing: 0.6px;
    white-space: nowrap;
  }
  .contacts svg { width: 16px; height: 16px; flex: none; }

  .ghost-brand {
    position: absolute;
    right: 22px; top: 108px;
    font-size: 56px;
    font-weight: 700;
    line-height: 1;
    color: var(--ghost);
    text-align: right;
  }
</style>
</head>
<body>

  <section class="card card--front" aria-label="Card front">
    <div class="brand"><span class="brand__mark"></span>TMW Home Crafting</div>
    <p class="website">www.<span class="accent">tmwhomecrafting</span>.com.au</p>
  </section>

  <section class="card card--back" aria-label="Card back">
    <div class="brand"><span class="brand__mark"></span>TMW Home Crafting</div>

    <div class="ghost-brand" aria-hidden="true">TMW<br>Home<br>Crafting</div>

    <span class="name-bar"></span>
    <div class="person">
      <h1 class="person__name"><span class="person__first">Dale</span> Whitford</h1>
      <p class="person__title">General Manager</p>
    </div>

    <ul class="contacts">
      <li>
        <svg viewBox="0 0 24 24" fill="var(--green)"><path d="M6.6 10.8a15.2 15.2 0 0 0 6.6 6.6l2.2-2.2a1 1 0 0 1 1-.25 11.4 11.4 0 0 0 3.6.57 1 1 0 0 1 1 1V20a1 1 0 0 1-1 1A17 17 0 0 1 3 4a1 1 0 0 1 1-1h3.5a1 1 0 0 1 1 1c0 1.25.2 2.45.57 3.57a1 1 0 0 1-.25 1z"/></svg>
        <span class="contacts__text">0400 555 018</span>
      </li>
      <li>
        <svg viewBox="0 0 24 24" fill="none" stroke="var(--green)" stroke-width="2"><circle cx="12" cy="12" r="9"/><path d="M3 12h18M12 3c3 3 3 15 0 18M12 3c-3 3-3 15 0 18"/></svg>
        <span class="contacts__text">www.<span class="accent">tmwhomecrafting</span>.com.au</span>
      </li>
      <li>
        <svg viewBox="0 0 24 24" fill="none" stroke="var(--green)" stroke-width="2"><rect x="3" y="6" width="18" height="13" rx="1"/><path d="M3 7l9 7 9-7"/></svg>
        <span class="contacts__text">info@<span class="accent">tmwhomecrafting</span>.com.au</span>
      </li>
      <li>
        <svg viewBox="0 0 24 24" fill="var(--green)"><path d="M12 2a7 7 0 0 0-7 7c0 5 7 13 7 13s7-8 7-13a7 7 0 0 0-7-7zm0 9.5A2.5 2.5 0 1 1 12 6.5a2.5 2.5 0 0 1 0 5z"/></svg>
        <span class="contacts__text">Riverbend, Tasmania, Australia</span>
      </li>
    </ul>
  </section>

</body>
</html>
```